Poster design for "A Frame" Sign

I need a design for an A Frame sign. Measurements and Specifications here:
http://www.trimboxdepot.com.au/pg/a-boards/ABPBBLKPRT-Print-Specs.pdf

Actually, it will need to be two designs, one with an arrow pointing left and one with an arrow pointing right, otherwise exactly the same.

LOGO to be used is attached. Colours of design should match logo and should also include orange tones.

The A Frame sign is to be put on the driveway of my home studio at a main road in a residential suburban area. Cars drive by at around 50 km/h, so there needs to be an eye catcher that there is a nurturing home massage studio here.

Logo can be left or right, somehow incorporated into the text below:
-
[Big header, ideally "LeHavre" font]
Sorela Healing
Massage Studio

[slightly smaller font, serif, with bullet points]
- Relaxation Massage
- Remedial Massage
- Pregnancy Massage
- Kahuna Massage

[big Arrow to the left/right - one for each side of the frame]

[sans serif font, same size as above]
Bookings essential!
ph 0491 578 264
www.sorelahealing.com.au

[serif font, same as above]
EFTPOS and instant health fund claims available.
-

Residential

f37022

```html
<!DOCTYPE html>
<html lang="en">
<head>
<meta charset="utf-8">
<title>Sorela Healing Massage Studio – A Frame Sign</title>
<link rel="stylesheet" href="https://fonts.googleapis.com/css2?family=Sniglet:wght@400;800&family=Patrick+Hand&family=Cabin:wght@600;700&display=swap">
<style>
  :root {
    --stage: #2c2f33;
    --peach: #f8dcaa;
    --apricot: #e9a868;
    --rust: #b0602f;
    --burnt: #9a4a25;
    --plum: #7a1442;
    --rose: #e8509a;
    --rose-deep: #c7317c;
    --white: #ffffff;
  }
  * { box-sizing: border-box; margin: 0; padding: 0; }
  html, body { width: 1200px; height: 900px; overflow: hidden; background: var(--stage); }

  .sign {
    position: absolute;
    left: 310px; top: 22px;
    width: 580px; height: 856px;
    background: linear-gradient(160deg, var(--peach) 0%, var(--apricot) 45%, var(--rust) 80%, var(--burnt) 100%);
    overflow: hidden;
  }

  .logo-disc {
    position: absolute;
    left: 208px; top: 32px;
    width: 162px; height: 162px;
    border-radius: 50%;
    background: var(--rose-deep);
  }

  .studio-name {
    position: absolute;
    left: 0; width: 100%;
    text-align: center;
    font-family: "Sniglet", sans-serif;
    font-weight: 800;
    color: var(--rose);
    line-height: 1;
  }
  .studio-name--main { top: 214px; font-size: 56px; }
  .studio-name--sub { top: 266px; font-size: 42px; }

  .treatment {
    position: absolute;
    width: 188px; height: 188px;
  }
  .treatment--relaxation { left: 49px;  top: 325px; }
  .treatment--kahuna     { left: 246px; top: 330px; }
  .treatment--remedial   { left: 105px; top: 498px; }
  .treatment--pregnancy  { left: 350px; top: 478px; }
  .treatment-label {
    font-family: "Cabin", sans-serif;
    font-weight: 700;
    font-size: 13px;
    fill: var(--white);
    letter-spacing: 0.3px;
  }

  .bookings {
    position: absolute;
    left: 255px; top: 672px;
    font-family: "Cabin", sans-serif;
    font-weight: 700;
    font-size: 19px;
    color: var(--plum);
    letter-spacing: 0.5px;
  }

  .direction-arrow {
    position: absolute;
    left: 72px; top: 681px;
    width: 478px; height: 120px;
  }
  .phone {
    position: absolute;
    left: 72px; top: 702px;
    width: 418px; height: 78px;
    display: flex; align-items: center; justify-content: center;
    font-family: "Patrick Hand", sans-serif;
    font-size: 76px;
    color: var(--plum);
    letter-spacing: 2px;
    line-height: 1;
  }

  .website {
    position: absolute;
    left: 0; width: 100%;
    top: 784px;
    text-align: center;
    font-family: "Cabin", sans-serif;
    font-weight: 700;
    font-size: 20px;
    color: var(--plum);
    letter-spacing: 0.4px;
  }

  .payment-band {
    position: absolute;
    left: 13px; top: 814px;
    width: 552px; height: 31px;
    background: var(--plum);
    display: flex; align-items: center; justify-content: center;
    font-family: "Cabin", sans-serif;
    font-weight: 600;
    font-size: 19px;
    color: var(--white);
    letter-spacing: 0.5px;
  }
</style>
</head>
<body>
  <main class="sign">
    <div class="logo-disc" aria-hidden="true"></div>

    <h1 class="studio-name studio-name--main">Sorela Healing</h1>
    <h2 class="studio-name studio-name--sub">Massage Studio</h2>

    <svg class="treatment treatment--relaxation" viewBox="-100 -100 200 200">
      <defs>
        <linearGradient id="tone-relax" x1="0" y1="0" x2="1" y2="1">
          <stop offset="0" stop-color="#c9a07e"/><stop offset="1" stop-color="#4a3a36"/>
        </linearGradient>
        <path id="arc-relax" d="M43,-74.5 A86,86 0 0 1 22.3,83.1"/>
      </defs>
      <circle r="96" fill="var(--plum)"/>
      <circle cx="-9" r="82" fill="url(#tone-relax)" role="img" aria-label="Photo of a relaxation massage"/>
      <text class="treatment-label"><textPath href="#arc-relax" startOffset="4">Relaxation Massage</textPath></text>
    </svg>

    <svg class="treatment treatment--kahuna" viewBox="-100 -100 200 200">
      <defs>
        <linearGradient id="tone-kahuna" x1="0" y1="0" x2="1" y2="1">
          <stop offset="0" stop-color="#f0ddc8"/><stop offset="1" stop-color="#8a5a3c"/>
        </linearGradient>
        <path id="arc-kahuna" d="M43,-74.5 A86,86 0 0 1 22.3,83.1"/>
      </defs>
      <circle r="96" fill="var(--plum)"/>
      <circle cx="-9" r="82" fill="url(#tone-kahuna)" role="img" aria-label="Photo of a kahuna massage"/>
      <text class="treatment-label"><textPath href="#arc-kahuna" startOffset="14">Kahuna Massage</textPath></text>
    </svg>

    <svg class="treatment treatment--remedial" viewBox="-100 -100 200 200">
      <defs>
        <linearGradient id="tone-remedial" x1="0" y1="0" x2="1" y2="1">
          <stop offset="0" stop-color="#3a3030"/><stop offset="1" stop-color="#c88a60"/>
        </linearGradient>
        <path id="arc-remedial" d="M43,-74.5 A86,86 0 0 1 22.3,83.1"/>
      </defs>
      <circle r="96" fill="var(--plum)"/>
      <circle cx="-9" r="82" fill="url(#tone-remedial)" role="img" aria-label="Photo of a remedial massage"/>
      <text class="treatment-label"><textPath href="#arc-remedial" startOffset="8">Remedial Massage</textPath></text>
    </svg>

    <svg class="treatment treatment--pregnancy" viewBox="-100 -100 200 200">
      <defs>
        <linearGradient id="tone-pregnancy" x1="0" y1="0" x2="1" y2="1">
          <stop offset="0" stop-color="#f6efe8"/><stop offset="1" stop-color="#caa184"/>
        </linearGradient>
        <path id="arc-pregnancy" d="M43,-74.5 A86,86 0 0 1 22.3,83.1"/>
      </defs>
      <circle r="96" fill="var(--plum)"/>
      <circle cx="-9" r="82" fill="url(#tone-pregnancy)" role="img" aria-label="Photo of a pregnancy massage"/>
      <text class="treatment-label"><textPath href="#arc-pregnancy" startOffset="4">Pregnancy Massage</textPath></text>
    </svg>

    <p class="bookings">Bookings Essential!</p>

    <svg class="direction-arrow" viewBox="0 0 478 120" aria-hidden="true">
      <polygon points="0,21 418,21 418,0 478,60 418,120 418,99 0,99" fill="var(--white)"/>
    </svg>
    <p class="phone">0491 578 264</p>

    <p class="website">www.sorelahealing.com.au</p>

    <p class="payment-band">EFTPOS and instant health fund claims available</p>
  </main>
</body>
</html>
```